Shampoo and Shower Gel Packaging Design

I need a new packaging design for a men shampoo and shower gel bottle. The packaging must me black (black bottle/package) and the logo should be also monochrom.
For example, black matte bottle and black shiny logo on the packaging (not mandatory).
the design must contain maximum 3 colors.
1. black
2. white (text)
3. grey/dark blue/dark green (colors will be the difference between products parfumes/smell/scences.

Design must be minimalist/elegant/discrete.
Updates

Please check the photos i added for pure inspiration.

Target Market(s)

brand exclusively for MEN - premium clients

Industry/Entity Type

Cosmetics

Font styles to use
Sans Serif

Colors
1b1b1b
5c5c5c
aaaaaa
ffffff
3176b5

Requirements
Must have
• black background
• minimalist design

```html
<!DOCTYPE html>
<html lang="en">
<head>
<meta charset="UTF-8">
<title>Shampoo for Men – Label</title>
<link rel="stylesheet" href="https://fonts.googleapis.com/css2?family=Open+Sans:wght@300;400&display=swap">
<style>
  :root {
    --backdrop: #d6d6d6;
    --label-black: #141414;
    --label-sheen: #262626;
    --text-white: #ececec;
    --mark-grey: #5c5c5c;
    --brand-grey: #aaaaaa;
  }
  html, body {
    margin: 0;
    padding: 0;
    width: 1200px;
    height: 1049px;
    overflow: hidden;
    background: var(--backdrop);
  }
  .canvas {
    position: relative;
    width: 1200px;
    height: 1049px;
  }
  .label {
    position: absolute;
    left: 255px;
    top: 0;
    width: 690px;
    height: 1049px;
    background: linear-gradient(90deg, var(--label-black) 0%, var(--label-sheen) 38%, var(--label-sheen) 55%, var(--label-black) 100%);
    font-family: "Open Sans", Arial, sans-serif;
    color: var(--text-white);
    text-align: center;
  }
  .product-name {
    position: absolute;
    top: 268px;
    left: 0;
    right: 0;
    margin: 0;
    font-weight: 400;
    font-size: 60px;
    letter-spacing: 14px;
    padding-left: 14px;
    line-height: 1;
  }
  .product-audience {
    position: absolute;
    top: 362px;
    left: 0;
    right: 0;
    margin: 0;
    font-weight: 400;
    font-size: 40px;
    letter-spacing: 9px;
    padding-left: 9px;
    line-height: 1;
  }
  .emblem {
    position: absolute;
    top: 446px;
    left: 220px;
    width: 250px;
    height: 278px;
  }
  .brand {
    position: absolute;
    top: 862px;
    left: 0;
    right: 0;
    display: flex;
    flex-direction: column;
    align-items: center;
    gap: 14px;
  }
  .brand-dot {
    width: 26px;
    height: 26px;
    border-radius: 50%;
    background: var(--brand-grey);
  }
  .brand-name {
    font-weight: 300;
    font-size: 28px;
    letter-spacing: 10px;
    padding-left: 10px;
    color: var(--brand-grey);
    line-height: 1;
  }
</style>
</head>
<body>
  <main class="canvas">
    <section class="label">
      <h1 class="product-name">SHAMPOO</h1>
      <p class="product-audience">FOR MEN</p>
      <svg class="emblem" viewBox="0 0 250 278" role="img" aria-label="Striped shield emblem of the product line">
        <rect x="0" y="0" width="250" height="278" rx="6" fill="var(--mark-grey)" opacity="0.55"/>
      </svg>
      <div class="brand">
        <span class="brand-dot"></span>
        <span class="brand-name">VELMOR</span>
      </div>
    </section>
  </main>
</body>
</html>
```